Hawaii Luxury Real Estate Sales Broker needs Stationery Design Project

I am a high end property Broker here in Hawaii. I am trying to distinguish myself and my name as a brand as opposed to just being one in hundreds of Realtors out there. I am fortunate to have positioned myself into this particular market and would like to continue to grow my business here by finding the right added touch of classy detail that will make me stand out to Buyers and Sellers of this caliber. I am looking to brand myself via stationary and ads that I can place internationally. The high net worth individuals that I will be reaching out to make this a project that needs to emulate class and sophistication but with a bit of a feminine appeal as I am a woman. :-) Because I live in Hawaii I think this too may be able to play a part of the elegance in design based on the beauty that surrounds us here in the Pacific.

Target Market(s)

High Net Worth Individuals (Calloway List, Birch Ln Gazette, Private Jet owners)

Industry/Entity Type

Business

Requirements
Must have
• My initials. I would like to see my name or initials always at their fingertips as I want them to be thinking of me as their Realtor.
Should not have
• Nothing too cheesy or touristy. It is important that this is something I can confidently send to high net worth individuals.

```html
<!DOCTYPE html>
<html lang="en">
<head>
<meta charset="utf-8">
<title>Lena Castell – Desk Notepad</title>
<link rel="stylesheet" href="https://fonts.googleapis.com/css2?family=Caveat:wght@500&family=Source+Sans+3:wght@400&display=swap">
<style>
  :root {
    --backdrop: #efede9;
    --pad: #cdc9c3;
    --pad-edge: #bdb8b1;
    --sheet: #ffffff;
    --rule: #6f6f6f;
    --ink: #1c1c1c;
    --gold: #b09444;
  }
  * { margin: 0; padding: 0; box-sizing: border-box; }
  html, body {
    width: 985px; height: 1200px; overflow: hidden;
    background: var(--backdrop);
  }
  .notepad {
    position: absolute; left: 52px; top: 32px;
    width: 880px; height: 1136px;
    background: var(--pad);
    border: 1px solid var(--pad-edge);
    font-family: "Source Sans 3", "Myriad Pro", sans-serif;
    color: var(--ink);
  }
  .desk-line {
    position: absolute; left: 76px; top: 176px;
    font-family: "Caveat", cursive;
    font-size: 30px; line-height: 1;
  }
  .brand {
    position: absolute; left: 345px; top: 150px;
    display: flex; align-items: center; gap: 16px;
  }
  .brand-mark {
    width: 22px; height: 22px; background: var(--gold);
  }
  .brand-name {
    font-size: 38px; font-weight: 400;
    letter-spacing: 7px; color: var(--ink);
  }
  .writing-sheet {
    position: absolute; left: 62px; top: 284px;
    width: 765px; height: 771px;
    background: var(--sheet);
    border-radius: 28px;
  }
  .ruled-lines {
    list-style: none;
    position: absolute; left: 14px; right: 14px; top: 16px;
  }
  .ruled-lines li {
    height: 28.5px;
    border-bottom: 1px dotted var(--rule);
  }
  .contact {
    position: absolute; left: 0; right: 0; top: 1074px;
    text-align: center; font-size: 18px; line-height: 25px;
  }
  .contact-row {
    display: flex; justify-content: center; align-items: center; gap: 6px;
  }
  .contact-row svg { width: 14px; height: 14px; fill: var(--ink); }
  .contact-row .item { display: inline-flex; align-items: center; gap: 6px; margin-right: 6px; }
</style>
</head>
<body>
  <main class="notepad">
    <p class="desk-line">From the desk of</p>
    <div class="brand">
      <span class="brand-mark"></span>
      <span class="brand-name">LENA CASTELL</span>
    </div>

    <section class="writing-sheet">
      <ol class="ruled-lines">
        <li></li><li></li><li></li><li></li><li></li>
        <li></li><li></li><li></li><li></li><li></li>
        <li></li><li></li><li></li><li></li><li></li>
        <li></li><li></li><li></li><li></li><li></li>
        <li></li><li></li><li></li><li></li><li></li>
      </ol>
    </section>

    <footer class="contact">
      <p class="contact-address">Complex Name, Street Name, Area, City Name,000 000</p>
      <p class="contact-row">
        <span class="item">
          <svg viewBox="0 0 16 16" aria-hidden="true"><circle cx="8" cy="8" r="7" fill="none" stroke="#1c1c1c" stroke-width="1.4"/><path d="M5 4.5l1.6-.4 1 2-1 .8c.5 1.1 1.3 1.9 2.4 2.4l.8-1 2 1-.4 1.6c-3.4.2-6.6-3-6.4-6.4z"/></svg>
          +1 808 555 0142
        </span>
        <span class="item">
          <svg viewBox="0 0 16 16" aria-hidden="true"><rect x="1" y="4" width="14" height="9" rx="1"/></svg>
          lena@castellmail.com
        </span>
        <span class="item">
          <svg viewBox="0 0 16 16" aria-hidden="true"><g fill="none" stroke="#1c1c1c" stroke-width="1.3"><circle cx="8" cy="8" r="6.5"/><ellipse cx="8" cy="8" rx="3" ry="6.5"/><path d="M1.5 8h13M2.5 4.8h11M2.5 11.2h11"/></g></svg>
          www.castellhomes.com
        </span>
      </p>
    </footer>
  </main>
</body>
</html>
```